Business Card Design Project

Business card based on attached logo

Todd Merrick
Todd@lorvantest.com
877-514-9073 ext. 318
Www.LorvanTest.com

Industry/Entity Type

Business

```html
<!DOCTYPE html>
<html lang="en">
<head>
<meta charset="utf-8">
<title>LorvanTest Business Cards</title>
<link rel="stylesheet" href="https://fonts.googleapis.com/css2?family=Arimo:wght@400;700&display=swap">
<style>
  :root {
    --page-bg: #ebebeb;
    --card-white: #ffffff;
    --card-edge: #cfcfcf;
    --brand-red: #d71f26;
    --brand-red-deep: #9e1a1e;
    --ink-black: #1b1b1b;
    --band-black-top: #2a2a2a;
    --band-black-bottom: #101010;
    --disc-white: #fbfbfb;
    --disc-shade: #e4e4e4;
    --text-body: #1f1f1f;
  }
  html, body {
    margin: 0;
    padding: 0;
    width: 1200px;
    height: 900px;
    overflow: hidden;
    background: var(--page-bg);
    font-family: "Arimo", Arial, sans-serif;
  }
  .stage {
    position: relative;
    width: 1200px;
    height: 900px;
  }
  .card {
    position: absolute;
    top: 289px;
    width: 430px;
    height: 244px;
    box-sizing: border-box;
    border: 1px solid var(--card-edge);
    overflow: hidden;
  }
  .card--front {
    left: 113px;
    background: linear-gradient(to bottom, var(--brand-red) 0%, var(--brand-red-deep) 100%);
  }
  .card--back {
    left: 656px;
    background: var(--card-white);
  }
  .brand-disc {
    position: absolute;
    border-radius: 50%;
    background: radial-gradient(circle at 45% 40%, var(--disc-white) 60%, var(--disc-shade) 100%);
    box-shadow: 0 2px 8px rgba(0,0,0,0.35);
    display: flex;
    align-items: center;
    justify-content: center;
  }
  .brand-disc--large {
    left: 132px;
    top: 39px;
    width: 166px;
    height: 166px;
  }
  .brand-disc--small {
    left: 172px;
    top: 157px;
    width: 86px;
    height: 86px;
    z-index: 2;
  }
  .brand-name {
    font-weight: 700;
    color: var(--ink-black);
    letter-spacing: -0.3px;
    white-space: nowrap;
  }
  .brand-disc--large .brand-name { font-size: 24px; }
  .brand-disc--small .brand-name { font-size: 12.5px; }
  .card__brand {
    position: absolute;
    right: 24px;
    top: 38px;
    font-size: 22px;
  }
  .card__holder {
    position: absolute;
    left: 21px;
    top: 25px;
    margin: 0;
    font-size: 25px;
    font-weight: 700;
    color: var(--brand-red);
  }
  .card__contact {
    position: absolute;
    left: 21px;
    top: 140px;
    margin: 0;
    font-size: 13.5px;
    line-height: 16px;
    color: var(--text-body);
    font-style: normal;
  }
  .card__band {
    position: absolute;
    left: 0;
    right: 0;
    bottom: 0;
    height: 49px;
    display: flex;
  }
  .card__band-dark {
    width: 215px;
    background: linear-gradient(to bottom, var(--band-black-top), var(--band-black-bottom));
  }
  .card__band-red {
    flex: 1;
    background: linear-gradient(to bottom, var(--brand-red), var(--brand-red-deep));
  }
</style>
</head>
<body>
<main class="stage">
  <section class="card card--front" aria-label="Card front">
    <div class="brand-disc brand-disc--large">
      <span class="brand-name">LorvanTest</span>
    </div>
  </section>

  <section class="card card--back" aria-label="Card back">
    <h1 class="card__holder">Todd Merrick</h1>
    <span class="brand-name card__brand">LorvanTest</span>
    <address class="card__contact">
      Todd@lorvantest.com<br>
      877-514-9073 ext. 318<br>
      Www.LorvanTest.com
    </address>
    <div class="card__band">
      <div class="card__band-dark"></div>
      <div class="card__band-red"></div>
    </div>
    <div class="brand-disc brand-disc--small">
      <span class="brand-name">LorvanTest</span>
    </div>
  </section>
</main>
</body>
</html>
```